Ward Compass Business Card Design*

We need a business card design for our company Ward Compass. Our company is specialized in providing online consulting services regarding medical institutions, hospitals and doctors. We work with patients worldwide looking to choose between healthcare providers. We have a website you may use as a reference, where we list doctors and clinics worldwide. So we target Medical providers as well as patients worldwide.
Target Market(s)
Medical Providers and patients around the world
Industry/Entity Type
Medical
Contact Information for Business Card
Salwa Kettani
CEO
+90 612 348 2175
info@wardcompass.example
www.wardcompass.example
14 Annakhil 7 H.R.B. Rabat, Morocco
Requirements
Must have
- Company logo/name on one full side, personal info and smaller logo and company name on the other side.
Nice to have
- Smart and elegant design

```html
<!DOCTYPE html>
<html lang="en">
<head>
<meta charset="utf-8">
<title>Ward Compass – Business Card</title>
<link rel="stylesheet" href="https://fonts.googleapis.com/css2?family=Nunito+Sans:wght@400;600;700&display=swap">
<style>
  :root {
    --navy: #1a4373;
    --grey: #808080;
    --paper: #f3f3f5;
    --ink: #3a3a3a;
    --faint: #e4e5ec;
    --backdrop: #e6e3de;
    --white: #ffffff;
  }
  * { box-sizing: border-box; margin: 0; padding: 0; }
  html, body {
    width: 900px; height: 1200px; overflow: hidden;
    background: var(--backdrop);
    font-family: "Nunito Sans", Arial, sans-serif;
  }
  .card {
    position: absolute; left: 70px; width: 760px; height: 440px;
    box-shadow: 0 4px 12px rgba(0,0,0,.18);
    overflow: hidden;
  }
  /* Front */
  .card--front { top: 140px; background: var(--navy); }
  .brand-lockup {
    position: absolute; left: 0; right: 0; top: 170px;
    display: flex; align-items: center; justify-content: center; gap: 22px;
  }
  .brand-mark { width: 92px; height: 92px; border-radius: 50%; background: var(--white); }
  .brand-name {
    color: var(--white); font-weight: 600; font-size: 46px; letter-spacing: 1px;
    text-transform: uppercase;
  }
  .front-url {
    position: absolute; left: 0; right: 0; bottom: 30px; text-align: center;
    color: var(--white); font-size: 16px; letter-spacing: .3px;
  }
  /* Back */
  .card--back { top: 640px; background: var(--paper); }
  .back-decor {
    position: absolute; left: 272px; top: 106px; width: 240px; height: 240px;
    border-radius: 50%; background: var(--faint);
  }
  .back-lockup {
    position: absolute; left: 62px; top: 196px;
    display: flex; align-items: center; gap: 12px;
  }
  .back-lockup .brand-mark { width: 56px; height: 56px; background: var(--navy); }
  .back-lockup .brand-name { color: var(--navy); font-size: 25px; letter-spacing: .5px; }
  .divider {
    position: absolute; left: 382px; top: 170px; width: 1px; height: 110px; background: var(--ink);
  }
  .person { position: absolute; left: 410px; top: 164px; }
  .person-name { font-size: 26px; color: var(--ink); letter-spacing: .3px; line-height: 1.1; }
  .person-name strong { color: var(--navy); font-weight: 700; }
  .person-role { font-size: 18px; color: var(--ink); margin-top: 4px; }
  .contact-list { list-style: none; margin-top: 26px; }
  .contact-list li {
    display: flex; align-items: center; gap: 10px;
    font-size: 18px; color: var(--ink); height: 27px;
  }
  .contact-icon { width: 19px; height: 19px; flex: none; }
  .bottom-band { position: absolute; left: 0; right: 0; bottom: 0; height: 24px; display: flex; }
  .bottom-band span { flex: 1; }
  .band-navy { background: var(--navy); }
  .band-grey { background: var(--grey); }
</style>
</head>
<body>
  <section class="card card--front">
    <div class="brand-lockup">
      <div class="brand-mark"></div>
      <div class="brand-name">Ward Compass</div>
    </div>
    <div class="front-url">www.wardcompass.example</div>
  </section>

  <section class="card card--back">
    <div class="back-decor"></div>
    <div class="back-lockup">
      <div class="brand-mark"></div>
      <div class="brand-name">Ward Compass</div>
    </div>
    <div class="divider"></div>
    <div class="person">
      <div class="person-name"><strong>SALWA</strong> KETTANI</div>
      <div class="person-role">CEO</div>
      <ul class="contact-list">
        <li>
          <svg class="contact-icon" viewBox="0 0 20 20" aria-hidden="true">
            <circle cx="10" cy="10" r="10" fill="#1a4373"/>
            <path d="M7 5.5l1.6 2.3-1 1.1c.6 1.3 1.5 2.2 2.7 2.8l1.1-1 2.3 1.5-.6 1.9c-3.8-.3-6.5-3.1-7-6.9z" fill="#fff"/>
          </svg>
          +90 612 348 2175
        </li>
        <li>
          <svg class="contact-icon" viewBox="0 0 20 20" aria-hidden="true">
            <circle cx="10" cy="10" r="10" fill="#1a4373"/>
            <rect x="5.5" y="7" width="9" height="6.5" fill="#fff"/>
            <path d="M5.5 7l4.5 3.6L14.5 7" fill="none" stroke="#1a4373" stroke-width="1"/>
          </svg>
          info@wardcompass.example
        </li>
      </ul>
    </div>
    <div class="bottom-band"><span class="band-navy"></span><span class="band-grey"></span></div>
  </section>
</body>
</html>
```